Tradelume.ai

Australian based application building technology company. website (tradelume.ai) servicing the retail and shopping industries, IoT
Similar services to https://vextrio.com/.
Logo attached

Target Market(s)

Technology Retail

Industry/Entity Type

It Company

Number of Pages Required

2 page

Font styles to use
Other font styles liked:
• We will supply

Colors
ec1f27

Requirements
Must have
• responsive, extra small, small, medium, large, wide
Nice to have
• Modern, sophisticated, current and ON trende
Should not have
• Over saturation, keep it simple, smart and easy navigation

```html
<!DOCTYPE html>
<html lang="en">
<head>
<meta charset="utf-8">
<title>Tradelume.ai</title>
<link href="https://fonts.googleapis.com/css2?family=Raleway:wght@300;400;500;600;700;800&display=swap" rel="stylesheet">
<style>
:root{
  --brand:#ec1f27;
  --ink:#1e1e1e;
  --body:#4a4a4a;
  --muted:#777;
  --white:#ffffff;
  --band:#f4f4f4;
  --hero-a:#4a4c52;
  --hero-b:#8b8e94;
  --dark-overlay:#3c3a38;
}
*{box-sizing:border-box;margin:0;padding:0}
html,body{width:1200px;height:2740px;overflow:hidden}
body{font-family:"Raleway",Arial,sans-serif;color:var(--body);background:var(--white);position:relative}
.abs{position:absolute}
.btn{position:absolute;display:flex;align-items:center;justify-content:center;border-radius:30px;font-size:16px;font-weight:600;letter-spacing:.3px;text-transform:uppercase}
.btn-solid{background:var(--brand);color:var(--white)}
.btn-outline{border:2px solid var(--brand);color:var(--brand);background:transparent}

/* hero */
.hero{position:absolute;left:0;top:0;width:1200px;height:637px;background:linear-gradient(135deg,var(--hero-a),var(--hero-b) 55%,#5b5e64)}
.hero-photo{position:absolute;inset:0;background:radial-gradient(ellipse at 55% 45%,rgba(170,190,215,.55),rgba(60,62,68,.2) 60%,rgba(40,40,44,.4))}
.logo{position:absolute;left:75px;top:32px;display:flex;align-items:center;gap:12px;font-size:29px;font-weight:500;color:var(--white);letter-spacing:.5px}
.logo-mark{width:34px;height:34px;border-radius:50%;border:4px solid var(--white)}
.nav{position:absolute;left:434px;top:43px;display:flex;gap:0;font-size:13px;font-weight:600;color:var(--white)}
.nav span{position:absolute;white-space:nowrap}
.login{left:1021px;top:33px;width:106px;height:37px;font-size:13px}
.hero-title{position:absolute;left:0;width:1200px;top:267px;text-align:center;color:var(--white);font-size:51px;font-weight:800;line-height:56px;letter-spacing:.5px}
.hero-cta{left:519px;top:393px;width:164px;height:47px}
.dots{position:absolute;top:589px;left:557px;display:flex;gap:6px}
.dots i{width:15px;height:15px;border-radius:50%;background:var(--white)}
.dots i:first-child{background:var(--brand)}

/* feature rows */
.row{position:absolute;left:0;width:1200px}
.row-white{background:var(--white)}
.row-band{background:var(--band)}
.row h2{position:absolute;font-size:36px;font-weight:400;color:var(--ink);letter-spacing:.5px;text-transform:uppercase}
.row p{position:absolute;font-size:16.5px;line-height:29.5px;color:var(--body)}
.photo{position:absolute}
.video{position:absolute;left:624px;top:53px;width:505px;height:335px;border:5px solid #d8d8d8;background:linear-gradient(90deg,#8c0a0c,#a01114 60%,#e2e2e2 62%,#f2f2f2)}
.play{position:absolute;left:220px;top:135px}

/* banner */
.banner{position:absolute;left:0;top:2192px;width:1200px;height:311px;background:linear-gradient(180deg,#5a5550,#4a4642 55%,#3b4146)}
.banner h3{position:absolute;left:0;width:1200px;top:72px;text-align:center;color:var(--white);font-size:33px;font-weight:400;line-height:42px;letter-spacing:.5px}
.banner-cta{left:519px;top:192px;width:164px;height:48px}

/* footer */
.footer{position:absolute;left:0;top:2503px;width:1200px;height:237px;background:var(--white)}
.f-logo{position:absolute;left:75px;top:55px;display:flex;align-items:center;gap:10px;font-size:25px;font-weight:500;color:var(--brand)}
.f-logo .logo-mark{width:30px;height:30px;border-color:var(--brand)}
.copy{position:absolute;left:75px;top:105px;font-size:11px;line-height:21px;color:var(--muted)}
.social{position:absolute;left:75px;top:171px;display:flex;gap:20px}
.social i{width:15px;height:15px;border-radius:50%;background:#8a8a8a}
.f-col{position:absolute;top:42px}
.f-col h4{font-size:13px;font-weight:700;color:var(--brand);margin-bottom:12px;text-transform:uppercase}
.f-col li{list-style:none;font-size:13px;line-height:26.8px;color:var(--body)}
.email{position:absolute;left:886px;top:77px;width:241px;height:36px;border:1px solid #bdbdbd;border-radius:20px;font-size:11.5px;color:var(--ink);padding:0 18px;display:flex;align-items:center}
.signup{left:1021px;top:128px;width:106px;height:37px;font-size:13px}
.x10{position:absolute;right:6px;bottom:6px;font-size:11px;color:var(--ink)}
</style>
</head>
<body>

<header class="hero">
  <div class="hero-photo" role="img" aria-label="Hand holding a smartphone, tablet and laptop surrounded by floating app and network icons"></div>
  <div class="logo"><span class="logo-mark"></span>TRADELUME</div>
  <nav class="nav">
    <span style="left:0">HOME</span>
    <span style="left:78px">ABOUT</span>
    <span style="left:162px">SERVICES</span>
    <span style="left:264px">CLIENTS</span>
    <span style="left:357px">BLOG</span>
    <span style="left:433px">CONTACT US</span>
  </nav>
  <a class="btn btn-solid login">Log in</a>
  <h1 class="hero-title">VESTIBULUM VEL METUS SIT AMET<br>BIBENDUM TINCIDUNT</h1>
  <a class="btn btn-solid hero-cta">Read more</a>
  <div class="dots"><i></i><i></i><i></i><i></i></div>
</header>

<section class="row row-white" style="top:637px;height:443px">
  <h2 style="left:75px;top:75px">About Tradelume</h2>
  <p style="left:75px;top:134px;width:540px">Vestibulum vel metus sit amet turpis bibendum tincidunt vel sit amet quam. Pellentesque habitant morbi tristique senectus et netus et malesuada fames ac turpis egestas. Nunc consequat congue nulla eu imperdiet. Donec in est erat, id malesuada turpis. Nunc a dui id turpis convallis semper.</p>
  <a class="btn btn-outline" style="left:75px;top:314px;width:165px;height:48px">Read more</a>
  <div class="video" role="img" aria-label="Product video preview showing the in-store engagement app on two phones">
    <svg class="play" width="62" height="62" viewBox="0 0 62 62"><circle cx="31" cy="31" r="27" fill="none" stroke="#fff" stroke-width="5"/><path d="M25 19 L44 31 L25 43 Z" fill="#fff"/></svg>
  </div>
</section>

<section class="row row-band" style="top:1080px;height:371px">
  <div class="photo" role="img" aria-label="Shop assistant handing a shopping bag to a customer at a retail counter" style="left:75px;top:40px;width:423px;height:291px;background:linear-gradient(135deg,#d9d2cb,#b9b2aa 50%,#8c8884)"></div>
  <h2 style="left:554px;top:50px">Retail Sectors</h2>
  <p style="left:554px;top:108px;width:520px">Vestibulum vel metus sit amet turpis bibendum tincidunt vel sit amet quam. Pellentesque habitant morbi tristique senectus et netus et malesuada fames ac turpis egestas consequat congue nulla eu imperdiet.</p>
  <a class="btn btn-outline" style="left:554px;top:269px;width:165px;height:46px">Read more</a>
</section>

<section class="row row-white" style="top:1451px;height:370px">
  <h2 style="left:137px;top:50px">Shopping Industries</h2>
  <p style="left:137px;top:108px;width:520px">Vestibulum vel metus sit amet turpis bibendum tincidunt vel sit amet quam. Pellentesque habitant morbi tristique senectus et netus et malesuada fames ac turpis egestas consequat congue nulla eu imperdiet.</p>
  <a class="btn btn-outline" style="left:137px;top:268px;width:165px;height:46px">Read more</a>
  <div class="photo" role="img" aria-label="Woman shopping online on a laptop beside colourful shopping bags" style="left:706px;top:37px;width:423px;height:293px;background:linear-gradient(135deg,#e8e3dc,#d4ccc3 55%,#c9a9a6)"></div>
</section>

<section class="row row-band" style="top:1821px;height:371px">
  <div class="photo" role="img" aria-label="Hands holding a tablet showing an IoT network diagram on a café table" style="left:75px;top:42px;width:423px;height:289px;background:linear-gradient(135deg,#bfc4c6,#8f8f88 55%,#5d564c)"></div>
  <h2 style="left:554px;top:50px">IoT Firms</h2>
  <p style="left:554px;top:108px;width:520px">Vestibulum vel metus sit amet turpis bibendum tincidunt vel sit amet quam. Pellentesque habitant morbi tristique senectus et netus et malesuada fames ac turpis egestas consequat congue nulla eu imperdiet.</p>
  <a class="btn btn-outline" style="left:554px;top:269px;width:165px;height:46px">Read more</a>
</section>

<section class="banner" role="img" aria-label="Dimmed view of a harbour city skyline at dusk">
  <h3>AUSTRALIAN BASED APPLICATION BUILDING<br>TECHNOLOGY COMPANY</h3>
  <a class="btn btn-solid banner-cta">Read more</a>
</section>

<footer class="footer">
  <div class="f-logo"><span class="logo-mark"></span>TRADELUME</div>
  <div class="copy">Copyright © 2017, Company Name.<br>All Right Reserved</div>
  <div class="social"><i></i><i></i><i></i><i></i><i></i><i></i></div>

  <div class="f-col" style="left:342px"><h4>Product</h4><ul><li>Vestibulum</li><li>Ante ipsum primis</li><li>Faucibus orci</li><li>Luctus et ultrices</li><li>Posuere</li></ul></div>
  <div class="f-col" style="left:531px"><h4>Resources</h4><ul><li>Vestibulum</li><li>Ante ipsum primis</li><li>Faucibus orci</li><li>Luctus et ultrices</li><li>Posuere</li></ul></div>
  <div class="f-col" style="left:721px"><h4>Support</h4><ul><li>Vestibulum</li><li>Ante ipsum primis</li><li>Faucibus orci</li><li>Luctus et ultrices</li><li>Posuere</li></ul></div>
  <div class="f-col" style="left:889px"><h4>Newsletter sign up</h4></div>
  <div class="email">Enter Email Adress</div>
  <a class="btn btn-outline signup">Sign up</a>
  <div class="x10">X10</div>
</footer>

</body>
</html>
```